Kestrel Facilities Business Card Design

We would now like to design business cards with the new Kestrel Facilities logo

Target Market(s)

Professional

Industry/Entity Type

Professional services

Contact Information for Business Card

Employee name, title, phone number, email address, corporate office address and logo.

Font styles to use
Sans Serif

Colors
0054AA
0677BA
7BADD7
CADEEF
E8F1F8

Requirements
Must have
• My logo
Should not have
• any other pictures or images besides my logo

```html
<!DOCTYPE html>
<html lang="en">
<head>
<meta charset="utf-8">
<title>Kestrel Facilities – Business Card</title>
<link href="https://fonts.googleapis.com/css2?family=Oswald:wght@600&family=Montserrat:wght@400;500&display=swap" rel="stylesheet">
<style>
  :root{
    --bg:#e6e8eb;
    --card-white:#ffffff;
    --brand-blue:#0a6fe0;
    --brand-deep:#0054aa;
    --back-blue:#0a78e6;
    --text-grey:#555a60;
    --line-blue:#1a7be6;
  }
  *{margin:0;padding:0;box-sizing:border-box;}
  html,body{width:1200px;height:800px;overflow:hidden;background:var(--bg);}
  .canvas{width:1200px;height:800px;display:flex;flex-direction:column;align-items:center;justify-content:center;gap:44px;}
  .card{width:580px;height:331px;position:relative;box-shadow:0 6px 18px rgba(0,0,0,.12);}

  /* front */
  .card--front{background:var(--card-white);border-bottom:3px solid var(--brand-blue);}
  .wordmark{font-family:"Oswald",sans-serif;font-weight:600;text-transform:uppercase;letter-spacing:1px;display:flex;align-items:center;}
  .card--front .wordmark{position:absolute;right:40px;top:40px;font-size:26px;color:var(--brand-blue);gap:10px;}
  .wordmark__square{width:22px;height:22px;background:currentColor;display:inline-block;}
  .person{position:absolute;left:40px;top:176px;}
  .person__name{font-family:"Oswald",sans-serif;font-weight:600;font-size:26px;color:var(--brand-blue);letter-spacing:.5px;line-height:1;}
  .person__title{font-family:"Montserrat",sans-serif;font-size:13px;color:var(--text-grey);margin-top:4px;}
  .divider{position:absolute;left:40px;right:40px;top:238px;height:1px;background:var(--line-blue);}
  .contacts{position:absolute;left:40px;right:40px;top:254px;display:flex;justify-content:space-between;font-family:"Montserrat",sans-serif;font-size:11.5px;color:var(--text-grey);line-height:1.6;}
  .contact-group__row{display:flex;align-items:center;gap:6px;}
  .icon{width:11px;height:11px;flex:none;}

  /* back */
  .card--back{background:var(--back-blue);display:flex;align-items:center;justify-content:center;}
  .card--back .wordmark{font-size:44px;color:var(--brand-deep);gap:16px;}
  .card--back .wordmark__square{width:36px;height:36px;}
</style>
</head>
<body>
<main class="canvas">
  <section class="card card--front" aria-label="Business card front">
    <div class="wordmark"><span class="wordmark__square"></span>Kestrel Facilities</div>
    <div class="person">
      <div class="person__name">DANIEL HARPER</div>
      <div class="person__title">President</div>
    </div>
    <div class="divider"></div>
    <div class="contacts">
      <div class="contact-group">
        <div>4120 Birchwood Court</div>
        <div>Fairbanks, Alaska 99701</div>
      </div>
      <div class="contact-group">
        <div class="contact-group__row">
          <svg class="icon" viewBox="0 0 12 12"><path d="M3 1 L5 3.5 L4 5 Q5 7 7 8 L8.5 7 L11 9 L10 11 Q5 11 1 5 Q1 2 3 1Z" fill="var(--brand-blue)"/></svg>555-204-7731
        </div>
        <div class="contact-group__row">
          <svg class="icon" viewBox="0 0 12 12"><rect x="3" y="1" width="6" height="10" rx="1" fill="none" stroke="var(--brand-blue)" stroke-width="1.4"/></svg>555-318-6642
        </div>
      </div>
      <div class="contact-group">
        <div class="contact-group__row">
          <svg class="icon" viewBox="0 0 12 12"><rect x="1" y="2.5" width="10" height="7" fill="var(--brand-blue)"/><path d="M1.5 3 L6 6.5 L10.5 3" fill="none" stroke="#fff" stroke-width="1"/></svg>info@kestrelfacilities.com
        </div>
        <div class="contact-group__row">
          <svg class="icon" viewBox="0 0 12 12"><circle cx="6" cy="6" r="5" fill="var(--brand-blue)"/><path d="M1 6 H11 M6 1 Q3 6 6 11 M6 1 Q9 6 6 11" fill="none" stroke="#fff" stroke-width=".8"/></svg>www.kestrelfacilities.com
        </div>
      </div>
    </div>
  </section>

  <section class="card card--back" aria-label="Business card back">
    <div class="wordmark"><span class="wordmark__square"></span>Kestrel Facilities</div>
  </section>
</main>
</body>
</html>
```